Business card for a new cabinet shop company named Veloran Cabinets for high end cabinets

Design a business card, thinking dark rich green with colours to speak of high end luxury ie; cream, gold, black possibly

Mitchell Tarrowby
Director Craftsman
Email: info@veloranjoinery-example.com.au
Instagram : @veloran.cabinets

```html
<!DOCTYPE html>
<html lang="en">
<head>
<meta charset="utf-8">
<title>Veloran Cabinets – Business Card</title>
<link rel="stylesheet" href="https://fonts.googleapis.com/css2?family=Arimo:wght@400;700&display=swap">
<style>
  :root {
    --backdrop: #e3e3e3;
    --card: #1f3a2e;
    --card-deep: #16291f;
    --gold: #c9a55c;
    --cream: #f3ecdc;
    --emboss: #3a5c4b;
    --emboss-light: #5f8271;
  }
  * { margin: 0; padding: 0; box-sizing: border-box; }
  html, body { width: 1200px; height: 1200px; overflow: hidden; }
  body {
    background: var(--backdrop);
    font-family: "Arimo", Arial, sans-serif;
    position: relative;
  }
  .card {
    position: absolute;
    width: 687px;
    height: 392px;
    border-radius: 24px;
    overflow: hidden;
    background: linear-gradient(180deg, var(--card) 0%, var(--card-deep) 100%);
  }
  .card--front { left: 267px; top: 160px; }
  .card--back { left: 262px; top: 653px; }

  .wordmark { color: var(--gold); font-weight: 400; line-height: 1; white-space: nowrap; }
  .wordmark__name { display: block; }
  .wordmark__trade { display: block; }

  .card--front .wordmark { position: absolute; left: 44px; top: 32px; }
  .card--front .wordmark__name { font-size: 60px; letter-spacing: 1px; }
  .card--front .wordmark__trade { font-size: 28px; letter-spacing: 11px; margin-top: 8px; }

  .front-accent {
    position: absolute;
    left: 300px; top: 28px;
    width: 336px; height: 336px;
    border-radius: 50%;
    border: 14px solid var(--emboss);
    box-shadow: inset 2px 2px 0 rgba(255,255,255,0.06), 2px 2px 0 rgba(0,0,0,0.18);
  }

  .holder { position: absolute; left: 46px; top: 218px; }
  .holder__name { color: var(--gold); font-weight: 700; font-size: 26px; }
  .holder__role { color: var(--cream); font-size: 16px; margin-top: 5px; }

  .contacts { position: absolute; left: 46px; top: 290px; list-style: none; }
  .contacts li {
    display: flex; align-items: center; gap: 10px;
    color: var(--cream); font-size: 17px; height: 21px;
  }
  .contacts svg { width: 15px; height: 15px; flex: none; }

  .card--back .brand {
    position: absolute; inset: 0;
    display: flex; align-items: center; justify-content: center; gap: 34px;
    padding-bottom: 4px;
  }
  .brand__dot {
    width: 146px; height: 146px; border-radius: 50%;
    border: 4px solid var(--emboss);
  }
  .card--back .wordmark { color: var(--emboss-light); }
  .card--back .wordmark__name { font-size: 68px; letter-spacing: 1px; }
  .card--back .wordmark__trade { font-size: 32px; letter-spacing: 14px; margin-top: 10px; }
</style>
</head>
<body>
  <section class="card card--front" aria-label="Card front">
    <span class="front-accent" aria-hidden="true"></span>
    <div class="wordmark">
      <span class="wordmark__name">Veloran</span>
      <span class="wordmark__trade">CABINETS</span>
    </div>
    <div class="holder">
      <p class="holder__name">Mitchell Tarrowby</p>
      <p class="holder__role">Director Craftsman</p>
    </div>
    <ul class="contacts">
      <li>
        <svg viewBox="0 0 16 16" aria-hidden="true"><rect x="1" y="4" width="14" height="9" fill="var(--gold)"/><path d="M1 4l7 5 7-5" fill="none" stroke="var(--card)" stroke-width="1.3"/></svg>
        info@veloranjoinery-example.com.au
      </li>
      <li>
        <svg viewBox="0 0 16 16" aria-hidden="true"><circle cx="8" cy="8" r="6.5" fill="var(--gold)"/><path d="M5 4c2 1 1 3 3 3s1 3 2 4M10 3c0 2 2 2 3 3" fill="none" stroke="var(--card)" stroke-width="1.2"/></svg>
        www.veloranjoinery-example.com.au
      </li>
      <li>
        <svg viewBox="0 0 16 16" aria-hidden="true"><circle cx="8" cy="8" r="6.5" fill="var(--gold)"/></svg>
        @veloran.cabinets
      </li>
    </ul>
  </section>

  <section class="card card--back" aria-label="Card back">
    <div class="brand">
      <span class="brand__dot" aria-hidden="true"></span>
      <div class="wordmark">
        <span class="wordmark__name">Veloran</span>
        <span class="wordmark__trade">CABINETS</span>
      </div>
    </div>
  </section>
</body>
</html>
```